Bramblewood Card Company Business Cards

We are a trading card store with Glimmorax, sports and other TCG cards, we need a business card design that encompasses a clean cut, modern style with a retro flare. website is bramblewoodcardco.com for reference. Can utilize a comic book era feel or a more modern outdoor feel to utilize the "Pacific Northwest" elements of tress, mountains, etc.

Industry/Entity Type

Trading cards and collectibles

Contact Information for Business Card

business name, email address, phone number, name, owner job title

Font styles to use
Sans Serif

```html
<!DOCTYPE html>
<html lang="en">
<head>
<meta charset="utf-8">
<title>Bramblewood Card Company – Business Cards</title>
<link href="https://fonts.googleapis.com/css2?family=Montserrat:wght@800&family=Arimo:wght@400;700&display=swap" rel="stylesheet">
<style>
  :root {
    --stage: #e9ecee;
    --sky: #0fbfe0;
    --slate: #737373;
    --paper: #ffffff;
    --ink-light: #ffffff;
  }
  * { margin: 0; padding: 0; box-sizing: border-box; }
  html, body { width: 1200px; height: 874px; overflow: hidden; background: var(--stage); }
  .canvas {
    position: relative; width: 1200px; height: 874px;
    display: flex; flex-direction: column; align-items: center; justify-content: center; gap: 40px;
  }
  .card {
    position: relative; width: 660px; height: 377px; border-radius: 22px; overflow: hidden;
    box-shadow: 0 6px 18px rgba(0,0,0,.15);
  }
  .card-front { background: var(--sky); display: flex; align-items: center; justify-content: center; }
  .brand {
    display: flex; align-items: center; gap: 14px;
    font-family: "Montserrat", sans-serif; font-weight: 800; font-size: 30px;
    letter-spacing: 1px; text-transform: uppercase; line-height: 1.1; text-align: center;
  }
  .brand-dot { width: 22px; height: 22px; border-radius: 50%; flex: none; }
  .card-front .brand { color: var(--ink-light); }
  .card-front .brand-dot { background: var(--ink-light); }
  .card-back { background: var(--slate); }
  .card-back .backdrop { position: absolute; inset: 0; }
  .card-back .brand {
    position: absolute; left: 0; right: 0; top: 88px; justify-content: center;
    color: var(--slate); font-size: 26px;
  }
  .card-back .brand-dot { background: var(--sky); }
  .contact {
    position: absolute; left: 34px; bottom: 40px; list-style: none;
    font-family: "Arimo", sans-serif; font-size: 17px; color: var(--ink-light); line-height: 1.45;
  }
  .contact li { display: flex; align-items: center; gap: 10px; }
  .contact svg { width: 14px; height: 14px; fill: var(--sky); flex: none; }
  .person {
    position: absolute; right: 40px; bottom: 30px; text-align: right;
    font-family: "Arimo", sans-serif;
  }
  .person-name { font-weight: 700; font-size: 30px; color: var(--sky); }
  .person-title { font-size: 18px; color: var(--ink-light); }
</style>
</head>
<body>
<main class="canvas">
  <section class="card card-front" aria-label="Card front">
    <div class="brand"><span class="brand-dot"></span><span>Bramblewood<br>Card Company</span></div>
  </section>

  <section class="card card-back" aria-label="Card back">
    <svg class="backdrop" viewBox="0 0 660 377" preserveAspectRatio="none" aria-hidden="true">
      <path d="M0 0 H660 V212 L300 302 L0 92 Z" fill="var(--paper)"/>
      <path d="M0 104 L300 312 L660 222" fill="none" stroke="var(--sky)" stroke-width="7"/>
    </svg>
    <div class="brand"><span class="brand-dot"></span><span>Bramblewood<br>Card Company</span></div>
    <ul class="contact">
      <li><svg viewBox="0 0 24 24"><path d="M6.6 10.8a15 15 0 0 0 6.6 6.6l2.2-2.2c.3-.3.7-.4 1-.2 1.1.4 2.3.6 3.6.6.6 0 1 .4 1 1V20c0 .6-.4 1-1 1A17 17 0 0 1 3 4c0-.6.4-1 1-1h3.5c.6 0 1 .4 1 1 0 1.3.2 2.5.6 3.6.1.3 0 .7-.2 1z"/></svg>555-204-7318</li>
      <li><svg viewBox="0 0 24 24"><path d="M2 5h20v14H2z M2 5l10 8 10-8" /></svg>info@bramblewoodcardco.com</li>
      <li><svg viewBox="0 0 24 24"><circle cx="12" cy="12" r="10"/></svg>www.bramblewoodcardco.com</li>
    </ul>
    <div class="person">
      <div class="person-name">Alden Marsh</div>
      <div class="person-title">President</div>
    </div>
  </section>
</main>
</body>
</html>
```